New Business Card Design Project LORVANTI-Italy

we are LORVANTI-Italy
our company in the market for 3 years we are luxury cosmetic company and its about time for a facelift :)
i will like to have elegant luxurious and unique business card
that will give the person that get it a unique, luxurious and elegant impression
I'm VERY OPEN FOR NEW IDEAS , even duo i add a few files of things that i see on line and i like them

i add my logo as well
my website is LORVANTI.COM
(if you would like to see the main style that we have)

Target Market(s)

adult that have money :)

Industry/Entity Type

Business

Contact Information for Business Card

Name - Dario Lorvanti
Position - CEO and CO Founder
address - 4817 E Halvern
telephone - 555-384-1926
email - dario@lorvanti.com
fax - 555-384-1926
website - LORVANTI.COM

Colors
000000
959595
fbee3e
ffffff

Requirements
Must have
• big logo in GOLD color
• elegant look
• impressive
Nice to have
• not must but maybe classy pattern background
• not must but maybe emblem
• maybe clear plastic business card
Should not have
• colors
• images

```html
<!DOCTYPE html>
<html lang="en">
<head>
<meta charset="utf-8">
<title>LORVANTI Italy – Business Card</title>
<link rel="stylesheet" href="https://fonts.googleapis.com/css2?family=Cormorant+Garamond:wght@500&family=Rubik:wght@400;500&display=swap">
<style>
  :root {
    --backdrop: #121212;
    --card: #262527;
    --gold: #d9b526;
    --ink-light: #b9b8bb;
    --serif: "Cormorant Garamond", serif;
    --sans: "Rubik", sans-serif;
  }
  * { margin: 0; padding: 0; box-sizing: border-box; }
  html, body { width: 1200px; height: 800px; overflow: hidden; background: var(--backdrop); }
  .stage {
    width: 1200px; height: 800px;
    display: flex; align-items: center; justify-content: center; gap: 40px;
  }
  .card {
    position: relative;
    width: 540px; height: 309px;
    background: var(--card);
    box-shadow: 0 18px 40px rgba(0,0,0,.55);
  }

  /* Front */
  .card--front {
    display: flex; flex-direction: column; align-items: center; justify-content: center;
  }
  .brand-mark {
    width: 92px; height: 92px;
    border: 3px solid var(--gold);
    border-radius: 50%;
    margin-bottom: 14px;
  }
  .brand-name {
    font-family: var(--serif);
    font-weight: 500;
    font-size: 54px;
    letter-spacing: 3px;
    line-height: 1;
    color: var(--gold);
  }
  .brand-rule {
    width: 300px; height: 2px;
    background: var(--gold);
    margin: 10px 0 8px;
  }
  .brand-origin {
    font-family: var(--serif);
    font-weight: 500;
    font-size: 16px;
    letter-spacing: 3px;
    color: var(--gold);
  }

  /* Back */
  .card--back {
    display: flex; align-items: center;
    padding: 0 0 0 70px;
  }
  .back-mark {
    width: 150px; height: 150px;
    border: 3px solid var(--gold);
    border-radius: 50%;
    flex: none;
  }
  .divider {
    width: 2px; height: 150px;
    background: var(--gold);
    margin: 0 26px 0 44px;
    flex: none;
  }
  .contact { font-family: var(--sans); font-size: 13px; line-height: 1.55; color: var(--ink-light); }
  .contact__name { font-weight: 500; font-size: 17px; color: var(--gold); text-transform: uppercase; letter-spacing: .5px; }
  .contact__label { color: var(--gold); font-weight: 500; }
  .contact__web { color: var(--gold); font-weight: 500; margin-top: 2px; }
</style>
</head>
<body>
<main class="stage">
  <section class="card card--front" aria-label="Card front">
    <div class="brand-mark"></div>
    <div class="brand-name">LORVANTI</div>
    <div class="brand-rule"></div>
    <div class="brand-origin">ITALY</div>
  </section>

  <section class="card card--back" aria-label="Card back">
    <div class="back-mark"></div>
    <div class="divider"></div>
    <div class="contact">
      <div class="contact__name">Dario Lorvanti</div>
      <div>CEO &amp; CO Founder</div>
      <div>4817 E Halvern</div>
      <div><span class="contact__label">T</span> : 555-384-1926</div>
      <div><span class="contact__label">F</span> : 555-384-1926</div>
      <div><span class="contact__label">E</span> : dario@lorvanti.com</div>
      <div class="contact__web">LORVANTI.COM</div>
    </div>
  </section>
</main>
</body>
</html>
```